Contemporary new French wine brand needs logo and series of label design

to design a new contemporary logo and series of labels for a new French wine brand. We hope to attract not just current French wine drinkers but new ones who may appreciate a less traditional and more modern style.
Updates

Reason: we are wanting to extend the project for a few days more to receive more submissions since we had fewer designs submitted than we were expecting, maybe because of the holidays.

Target Market(s)

people who follow the arts community (eg. music, theatre, visual/video arts, dance) --- all mature ages.

Industry/Entity Type

French Wine

Requirements
Must have
• a clear, memorable treatment for the name MORIVAL with accompanying logo.
Nice to have
• embossing, matte/gloss refinement, tasteful foil stamping, coated stock for the whites to help the integrity of the paper in and out of ice buckets. A combo of say, three types of fonts; a semi custom font for the brand name Morival and maybe a script and one other.
Should not have
• not traditional French

```html
<!DOCTYPE html>
<html lang="fr">
<head>
<meta charset="utf-8">
<title>Morival — Sauvignon Blanc, Val de Loire</title>
<link rel="stylesheet" href="https://fonts.googleapis.com/css2?family=Tinos:wght@400;700&family=Arimo:wght@400&display=swap">
<style>
  :root {
    --label-night: #121016;
    --sky-deep: #1b1f3f;
    --sky-violet: #3a2a6a;
    --hill-ember: #d8452b;
    --hill-amber: #e8873a;
    --field-plum: #5a2a6e;
    --field-wine: #7a2238;
    --field-ochre: #b8722e;
    --field-shadow: #221a2a;
    --ink-white: #f4f1ec;
    --accent-red: #c8262c;
  }

  * { margin: 0; padding: 0; box-sizing: border-box; }

  html, body {
    width: 849px;
    height: 1200px;
    overflow: hidden;
    background: var(--label-night);
  }

  .wine-label {
    position: relative;
    width: 849px;
    height: 1200px;
    background: var(--label-night);
    overflow: hidden;
  }

  .label-artwork {
    position: absolute;
    left: 0;
    top: 300px;
    width: 849px;
    height: 900px;
    background:
      linear-gradient(180deg,
        var(--label-night) 0%,
        var(--sky-deep) 6%,
        var(--sky-violet) 13%,
        var(--hill-ember) 22%,
        var(--hill-amber) 28%,
        var(--field-wine) 38%,
        var(--field-plum) 52%,
        var(--field-ochre) 66%,
        var(--field-plum) 80%,
        var(--field-shadow) 92%,
        var(--label-night) 100%);
  }

  .brand-block {
    position: absolute;
    top: 110px;
    left: 0;
    width: 100%;
    text-align: center;
  }

  .brand-lockup {
    display: inline-flex;
    align-items: flex-start;
    gap: 14px;
  }

  .brand-name {
    font-family: "Tinos", "Times New Roman", serif;
    font-weight: 700;
    font-size: 132px;
    letter-spacing: -3px;
    color: var(--ink-white);
    line-height: 1;
  }

  .brand-dot {
    width: 26px;
    height: 26px;
    margin-top: 22px;
    border-radius: 50%;
    background: var(--accent-red);
  }

  .brand-rule {
    display: block;
    margin: 26px auto 0;
    width: 560px;
    height: 5px;
  }

  .wine-details {
    position: absolute;
    left: 0;
    bottom: 34px;
    width: 100%;
    text-align: center;
    color: var(--ink-white);
  }

  .varietal {
    font-family: "Tinos", "Times New Roman", serif;
    font-weight: 400;
    font-size: 46px;
    letter-spacing: 0.5px;
    line-height: 1.1;
  }

  .appellation {
    margin-top: 10px;
    font-family: "Arimo", Arial, sans-serif;
    font-size: 27px;
    line-height: 1.2;
  }
</style>
</head>
<body>
  <main class="wine-label">
    <div class="label-artwork" role="img" aria-label="Painted Loire valley landscape: deep blue night sky, glowing orange-red hills with a small farmhouse and trees, and sweeping rows of purple and ochre vines"></div>

    <header class="brand-block">
      <div class="brand-lockup">
        <h1 class="brand-name">Morival</h1>
        <span class="brand-dot" aria-hidden="true"></span>
      </div>
      <svg class="brand-rule" viewBox="0 0 560 5" aria-hidden="true">
        <rect x="0" y="0" width="560" height="5" fill="var(--accent-red)"/>
      </svg>
    </header>

    <footer class="wine-details">
      <p class="varietal">SAUVIGNON BLANC</p>
      <p class="appellation">Val De Loire</p>
    </footer>
  </main>
</body>
</html>
```